Veldmark Supplies Business Card

Professional business card that stand out to our potential customers. Front and back with clean modern design

Industry/Entity Type

Oil and gas

Contact Information for Business Card

Name, address, website , office phone and cell number

Requirements
Must have
• Editable files for each employee

```html
<!DOCTYPE html>
<html lang="en">
<head>
<meta charset="utf-8">
<title>Veldmark Supplies – Business Card</title>
<link href="https://fonts.googleapis.com/css2?family=Poppins:wght@300;400;600;700&display=swap" rel="stylesheet">
<style>
  :root {
    --page-bg: #e4e8e9;
    --card-dark: #222226;
    --brand-red: #e8262b;
    --brand-red-light: #f0553a;
    --brand-cyan: #12aed2;
    --text-light: #ffffff;
    --text-soft: #e9e9ec;
  }
  * { box-sizing: border-box; margin: 0; padding: 0; }
  html, body {
    width: 1200px; height: 960px; overflow: hidden;
    background: var(--page-bg);
    font-family: "Poppins", sans-serif;
  }
  .card {
    position: absolute; left: 250px;
    width: 701px; height: 401px;
    background: var(--card-dark);
    overflow: hidden;
  }
  .card--front { top: 60px; }
  .card--back { top: 500px; }

  /* Front */
  .front-pattern {
    position: absolute; inset: 0;
    background:
      radial-gradient(ellipse at 90% 8%, rgba(255,255,255,0.22), transparent 55%),
      linear-gradient(135deg, #1c1c20 0%, #26262b 60%, #1d1d21 100%);
  }
  .front-brand {
    position: absolute; left: 0; right: 0; top: 0; bottom: 0;
    display: flex; align-items: center; justify-content: center; gap: 14px;
  }
  .brand-square {
    width: 22px; height: 22px; background: var(--brand-red);
  }
  .front-brand .brand-name {
    font-weight: 600; font-size: 34px; letter-spacing: 2px;
    color: var(--text-light); text-transform: uppercase;
  }

  /* Back */
  .back-emblem {
    position: absolute; left: 411px; top: 0; width: 290px; height: 401px;
    background: linear-gradient(160deg, #f6a48c 0%, var(--brand-red-light) 35%, var(--brand-red) 75%);
  }
  .back-brand {
    position: absolute; left: 25px; top: 110px;
    display: flex; align-items: center; gap: 8px;
  }
  .back-brand .brand-square { width: 14px; height: 14px; }
  .back-brand .brand-name {
    font-weight: 600; font-size: 18px; letter-spacing: 1px;
    color: var(--text-light); text-transform: uppercase;
  }
  .name-band {
    position: absolute; left: 0; top: 175px; width: 285px; height: 57px;
    background: linear-gradient(90deg, var(--brand-red) 0%, var(--brand-red) 40%, rgba(232,38,43,0) 100%);
    padding: 5px 0 0 19px;
  }
  .person-name {
    font-size: 25px; line-height: 30px; color: var(--text-light); font-weight: 300;
  }
  .person-name .first { font-weight: 700; }
  .person-title {
    font-size: 14px; line-height: 18px; color: var(--text-light); font-weight: 400;
  }
  .address {
    position: absolute; left: 19px; top: 250px;
    font-size: 15px; line-height: 19px; color: var(--brand-cyan); font-weight: 400;
  }
  .contact-list {
    position: absolute; left: 26px; top: 303px; list-style: none;
  }
  .contact-list li {
    display: flex; align-items: center; gap: 10px;
    font-size: 14.5px; line-height: 18.5px; color: var(--text-soft); font-weight: 300;
  }
  .contact-list svg { width: 13px; height: 13px; flex: none; }
</style>
</head>
<body>

<section class="card card--front">
  <div class="front-pattern" role="img" aria-label="Repeating embossed brand pattern on dark background"></div>
  <div class="front-brand">
    <span class="brand-square"></span>
    <span class="brand-name">Veldmark Supplies</span>
  </div>
</section>

<section class="card card--back">
  <div class="back-emblem" role="img" aria-label="Large embossed red brand emblem decoration"></div>

  <div class="back-brand">
    <span class="brand-square"></span>
    <span class="brand-name">Veldmark Supplies</span>
  </div>

  <div class="name-band">
    <p class="person-name"><span class="first">Lenka</span> Horakova</p>
    <p class="person-title">Co-Founder &amp; CEO</p>
  </div>

  <p class="address">48 Ridgeway Lane,<br>Carrow, TX 79001</p>

  <ul class="contact-list">
    <li>
      <svg viewBox="0 0 16 16"><path d="M3 1.5l3 .5 1 3-1.6 1.3a9 9 0 0 0 4.3 4.3L11 9l3 1 .5 3-1.5 1.5C7 14.5 1.5 9 1.5 3z" fill="var(--brand-cyan)"/></svg>
      (432) 555-0147
    </li>
    <li>
      <svg viewBox="0 0 16 16"><rect x="4" y="1" width="8" height="14" rx="1.5" fill="none" stroke="var(--brand-red)" stroke-width="1.8"/></svg>
      (432) 555-0192
    </li>
    <li>
      <svg viewBox="0 0 16 16"><circle cx="8" cy="8" r="6.5" fill="none" stroke="var(--brand-cyan)" stroke-width="1.6"/><path d="M1.5 8h13M8 1.5c-3 3.5-3 9.5 0 13M8 1.5c3 3.5 3 9.5 0 13" fill="none" stroke="var(--brand-cyan)" stroke-width="1.2"/></svg>
      www.veldmarksupplies.com
    </li>
    <li>
      <svg viewBox="0 0 16 16"><rect x="1.5" y="4" width="13" height="9" rx="1" fill="var(--brand-red)"/><path d="M1.5 4.5l6.5 5 6.5-5" fill="none" stroke="#fff" stroke-width="1.2"/></svg>
      info@veldmarksupplies.com
    </li>
  </ul>
</section>

</body>
</html>
```